Advertising Flyer

Leaflet to be 99mm x 210mm
Colour on both sides, its a singular piece of paper, front and back. I'm looking for something exciting that I couldnt design myself.
To advertise our business.
We specialise in wedding and portrait photography, we also do commercial photography.
We are a husband and wife team.

Our website is: www.marwoodstudios.co.nz
Facebook: www.facebook.com/marwoodstudios

I have attached some files, please let me know if you would like more or different ones that you see on website/FB
Updates

Please only use the photos that I have uploaded. I have just added some graduation ones if those are what you want to use.

Target Market(s)

mainly women making the decision to purchase but has to appeal to male and female.25-45

Industry/Entity Type

Wedding

Requirements
Must have
• We would like the background colour to be black, as this is how our business cards and website appear.
Must use our, logo, web address and contact information.
we would like to mention facebook, and the fact that customers can finance wedding packages (subject to approval).
Will upload some photos that can be used, logo etc.

```html
<!DOCTYPE html>
<html lang="en">
<head>
<meta charset="utf-8">
<title>Marwood Studios – Wedding &amp; Portrait Photography Flyer</title>
<link rel="stylesheet" href="https://fonts.googleapis.com/css2?family=Great+Vibes&family=Open+Sans:wght@400;600&display=swap">
<style>
  :root {
    --bg: #000000;
    --teal: #2bb3a6;
    --white: #ffffff;
    --muted: #bdbdbd;
    --ampersand: #9c9c9c;
    --gown-light: #f4f3ef;
    --gown-shade: #c9c7c1;
  }
  html, body {
    margin: 0;
    padding: 0;
    width: 1200px;
    height: 2546px;
    overflow: hidden;
    background: var(--bg);
  }
  .flyer {
    display: block;
    width: 1200px;
    height: 2546px;
  }
  .script { font-family: "Great Vibes", cursive; }
  .sans { font-family: "Open Sans", sans-serif; }
  .headline-wedding { fill: var(--teal); }
  .headline-ampersand { fill: var(--ampersand); }
  .headline-portrait { fill: var(--white); font-weight: 400; }
  .intro-line { fill: var(--white); font-weight: 400; }
  .brand-name { fill: var(--white); font-weight: 600; }
  .brand-dot { fill: var(--white); }
  .contact-line { fill: var(--muted); font-weight: 400; }
</style>
</head>
<body>
<svg class="flyer" viewBox="0 0 1200 2546" xmlns="http://www.w3.org/2000/svg">
  <defs>
    <radialGradient id="fireworks-glow" cx="50%" cy="50%" r="50%">
      <stop offset="0%" stop-color="#3f8f3a"/>
      <stop offset="45%" stop-color="#1f4d22"/>
      <stop offset="100%" stop-color="#000000"/>
    </radialGradient>
    <linearGradient id="bride-tone" x1="0" y1="0" x2="1" y2="1">
      <stop offset="0%" stop-color="var(--gown-light)"/>
      <stop offset="100%" stop-color="var(--gown-shade)"/>
    </linearGradient>
  </defs>

  <rect class="background" width="1200" height="2546" fill="var(--bg)"/>

  <rect class="fireworks" x="560" y="40" width="560" height="520" rx="260"
        fill="url(#fireworks-glow)" role="img"
        aria-label="Colourful fireworks bursting in yellow, blue, green and red"/>

  <rect class="bride-photo" x="700" y="1310" width="430" height="1140" rx="110"
        fill="url(#bride-tone)" role="img"
        aria-label="Photograph of a bride in a white strapless gown and veil holding a bouquet"/>

  <text class="script headline-wedding" font-size="430"
        transform="translate(610 2080) rotate(-90)"
        textLength="1660" lengthAdjust="spacingAndGlyphs">Wedding</text>

  <text class="script headline-ampersand" font-size="260"
        transform="translate(700 1370) rotate(-90)">&amp;</text>

  <text class="sans headline-portrait" font-size="58"
        transform="translate(695 1280) rotate(-90)"
        textLength="950" lengthAdjust="spacingAndGlyphs">portrait photography</text>

  <text class="sans intro-line" font-size="50"
        transform="translate(165 2030) rotate(-90)"
        textLength="520" lengthAdjust="spacingAndGlyphs">We specialise in</text>

  <g class="brand">
    <circle class="brand-dot" cx="140" cy="2290" r="28"/>
    <text class="sans brand-name" x="185" y="2308" font-size="52">Marwood Studios</text>
    <text class="sans contact-line" x="112" y="2380" font-size="22">www.marwoodstudios.co.nz</text>
    <text class="sans contact-line" x="112" y="2414" font-size="22">www.facebook.com/marwoodstudios</text>
  </g>
</svg>
</body>
</html>
```